Norrell Advisory WA Business Card

Create an interesting, eye catching and colourful two sided business card. We are a business consulting operation assisting SME's improve all areas of their business. We provide consulting services to assist SME's to create a culture of continuous improvement, making a positive difference in the business. Our tag line is Small changes, big rewards. We want to create a well recognised, innovative brand that can be continued throughout our website, social media and email correspondence.

Target Market(s)

Small to Medium Enterprise Business Owners

Industry/Entity Type

Business Consultant

Contact Information for Business Card

Name of Business: Norrell Advisory - Steady Steps Real Results
Derek Holloway Ph 0407385510 Megan Holloway Ph 0407913847
Email norrelladvisorywa@mailbox-example.com
Web address TBA
FaceBook page TBA

BACKSIDE OF CARD

Providing assistance with:

• Organisation & Efficiency
• Revenue generation & Marketing
• Financial Management
• Production quality & delivery
• Systems & Process documentation
• Exit Strategy

Font styles to use
Other font styles liked:
• Calibri

Colors

Designer to choose colors to be used in the design.

Requirements
Must have
• Calibri font

```html
<!DOCTYPE html>
<html lang="en">
<head>
<meta charset="utf-8">
<title>Norrell Advisory WA Business Card</title>
<link rel="stylesheet" href="https://fonts.googleapis.com/css2?family=Open+Sans:wght@400;600;700&display=swap">
<style>
  :root {
    --backdrop: #e6e6e4;
    --card: #1d1d1e;
    --text-strong: #c9c9c9;
    --text-body: #b5b5b5;
    --text-muted: #8a8a8a;
    --wordmark: #d2d2d2;
    --orange: #f7a532;
    --yellow: #fde35a;
    --blue: #62b8dc;
    --red: #f26650;
    --green: #8cc545;
  }
  * { margin: 0; padding: 0; box-sizing: border-box; }
  html, body {
    width: 1125px; height: 1200px; overflow: hidden;
    background: var(--backdrop);
    font-family: "Open Sans", Calibri, sans-serif;
  }
  .canvas { position: relative; width: 1125px; height: 1200px; }
  .card {
    position: absolute; left: 166px; width: 800px; height: 455px;
    background: var(--card); border-radius: 22px; overflow: hidden;
  }
  .card--front { top: 103px; }
  .card--back { top: 620px; }

  .contact-block { position: absolute; left: 47px; top: 34px; }
  .person-name { font-size: 29px; font-weight: 600; color: var(--text-strong); line-height: 32px; }
  .person-phone { font-size: 24px; font-weight: 700; color: var(--text-strong); line-height: 27px; }
  .person + .person { margin-top: 19px; }

  .links { list-style: none; margin-top: 20px; }
  .links li { display: flex; align-items: center; gap: 9px; font-size: 17px; color: var(--text-body); line-height: 24px; }
  .links svg { width: 17px; height: 17px; flex: none; }

  .services-title { margin-top: 16px; font-size: 24px; font-weight: 600; color: var(--text-strong); line-height: 30px; }
  .services { list-style: none; margin-top: 2px; }
  .services li { font-size: 17px; color: var(--text-body); line-height: 24px; padding-left: 17px; position: relative; }
  .services li::before { content: "•"; position: absolute; left: 0; }

  .brand-art {
    position: absolute; left: 540px; top: 0; width: 260px; height: 455px;
    background: linear-gradient(160deg, var(--blue) 0%, var(--red) 30%, var(--yellow) 55%, var(--orange) 70%, var(--green) 100%);
    opacity: .9;
  }

  .brand-mark {
    position: absolute; left: 330px; top: 90px; width: 140px; height: 140px;
    background: var(--orange); border-radius: 14px;
  }
  .brand-name {
    position: absolute; left: 0; right: 0; top: 302px; text-align: center;
    font-size: 44px; font-weight: 700; color: var(--wordmark); letter-spacing: 1px; line-height: 50px;
  }
  .brand-tagline {
    position: absolute; left: 0; right: 0; top: 352px; text-align: center;
    font-size: 20px; font-weight: 600; color: var(--text-muted); letter-spacing: 5.5px;
  }
</style>
</head>
<body>
<main class="canvas">
  <section class="card card--front">
    <div class="contact-block">
      <div class="person">
        <p class="person-name">Derek Holloway</p>
        <p class="person-phone">0407385510</p>
      </div>
      <div class="person">
        <p class="person-name">Megan Holloway</p>
        <p class="person-phone">0407913847</p>
      </div>
      <ul class="links">
        <li><svg viewBox="0 0 17 17"><rect x="1" y="1" width="15" height="15" rx="2" fill="#b5b5b5"/></svg>norrelladvisorywa</li>
        <li><svg viewBox="0 0 17 17"><rect x="1" y="3.5" width="15" height="10" fill="#b5b5b5"/><path d="M1 3.5 L8.5 9.5 L16 3.5" stroke="#1d1d1e" stroke-width="1.4" fill="none"/></svg>norrelladvisorywa@mailbox-example.com</li>
        <li><svg viewBox="0 0 17 17"><circle cx="8.5" cy="8.5" r="7.5" fill="#b5b5b5"/><path d="M1 8.5 H16 M8.5 1 C5 5 5 12 8.5 16 M8.5 1 C12 5 12 12 8.5 16" stroke="#1d1d1e" stroke-width="1.2" fill="none"/></svg>www.norrelladvisorywa.example</li>
      </ul>
      <h2 class="services-title">Providing assistance with</h2>
      <ul class="services">
        <li>Organisation &amp; Efficiency • Exit Strategy</li>
        <li>Revenue generation &amp; Marketing</li>
        <li>Financial Management • Production quality &amp; delivery</li>
        <li>Systems &amp; Process documentation</li>
      </ul>
    </div>
    <div class="brand-art" role="img" aria-label="Colourful brand decoration area"></div>
  </section>

  <section class="card card--back">
    <div class="brand-mark"></div>
    <h1 class="brand-name">NORRELL ADVISORY</h1>
    <p class="brand-tagline">STEADY STEPS REAL RESULTS</p>
  </section>
</main>
</body>
</html>
```